Clean Modern Skin Product branding/ label.

I need a label for a skincare line. The company is Dermaloft but product names will vary. A couple products to list are:
Sensitive Cleanser, Lumeno, Repair, Halo up, Mendora, Mendora Plus, Mendora Intense, Tavelo, Balance and Vivanto.

I would like the color scheme to be muted greens, grays, tourquise. The bottles are white, boston shaped with pumps, and ounces are 2, 4, 8, 16 ounces. When I choose the design, I can give you exact label sizes. Along with the ingredience already on the product label.

The look I desire is clean, minimal. A modern, organic look. Ideas that come to mind are a Veloraine,https://www.veloraine-example.com/product/2846/37204/3-step/step-2-exfoliate/clarifying-lotion-1 and the simplicity of Bo Tarn.

Both styles high light the name, in this case Dermaloft, and then the specific product.

My product is clean utilizing pure ingredients rather that a bunch fillers and binders. When I work with my clients I normally will say we need to "restore the balance" from over use of harsh products. That is why this lines works. It restores the skin to it's natural state. The process is simple, so I would like the label to reflect that simplicity.

Target Market(s)

Anyone with sensitive skin. So gender neutral

Industry/Entity Type

Skin Care Product

Font styles to use
Serif
Sans Serif
Decorative

Colors
acd037
33b8a4
fcfefd
85cae6
d3d3d3

Requirements
Must have
• Logo, name of product and color identity for cleanser, Active products, moisturizers
• I am thinking we could have one color for a cleanser and a space where I can put a sticker on which cleanser it is. Acne Cleasner, Sensitive Cleanser, and Cleanser.
Nice to have
• Not sure....suprise me. I would like the font to stay the same on the DERMALOFT, but you can change color, or color of leaf.
Should not have
• Too busy, too crowded or look like every other skincare line

```html
<!DOCTYPE html>
<html lang="en">
<head>
<meta charset="utf-8">
<title>Dermaloft — Sensitive Cleanser Label</title>
<link rel="stylesheet" href="https://fonts.googleapis.com/css2?family=Roboto:wght@300;500;700&family=Source+Sans+3:wght@400&display=swap">
<style>
  :root {
    --board: #7b9195;
    --label: #ffffff;
    --splash: #a9e9e4;
    --splash-fade: rgba(169, 233, 228, 0);
    --name: #5b6165;
    --product: #4c6e7d;
    --leaf-green: #8dd50f;
    --spec-ink: #111111;
  }
  * { margin: 0; padding: 0; box-sizing: border-box; }
  html, body { width: 1200px; height: 1200px; overflow: hidden; }
  body {
    background: var(--board);
    position: relative;
    font-family: "Roboto", sans-serif;
  }
  .label {
    position: absolute;
    left: 270px; top: 212px;
    width: 550px; height: 649px;
    background: var(--label);
  }
  .label__splash {
    position: absolute;
    left: 46px; top: 64px;
    width: 456px; height: 140px;
    background:
      linear-gradient(90deg, var(--splash-fade) 0%, var(--splash) 6%, var(--splash) 94%, var(--splash-fade) 100%);
  }
  .label__brand {
    position: absolute;
    left: 46px; top: 64px;
    width: 456px; height: 140px;
    display: flex; align-items: center; justify-content: center;
    font-weight: 500;
    font-size: 78px;
    letter-spacing: -1px;
    color: var(--name);
  }
  .label__product {
    position: absolute;
    left: 121px; top: 210px;
    width: 307px; height: 44px;
    border-top: 1px solid var(--product);
    border-bottom: 1px solid var(--product);
    display: flex; align-items: center; justify-content: center;
    font-weight: 300;
    font-size: 36px;
    color: var(--product);
    white-space: nowrap;
  }
  .label__mark {
    position: absolute;
    left: 232px; top: 462px;
    width: 84px; height: 84px;
    border-radius: 50%;
    background: var(--leaf-green);
  }
  .label__tagline {
    position: absolute;
    left: 0; top: 546px;
    width: 550px;
    text-align: center;
    font-weight: 700;
    font-size: 26px;
    color: var(--leaf-green);
  }
  .spec {
    position: absolute;
    font-family: "Source Sans 3", sans-serif;
    font-size: 22px;
    line-height: 30.5px;
    color: var(--spec-ink);
  }
  .spec--splash { left: 56px; top: 267px; }
  .spec--product { left: 100px; top: 415px; }
  .spec--tagline { left: 140px; top: 706px; }
  .spec__title {
    position: absolute; left: 168px; top: 294px;
    font-family: "Source Sans 3", sans-serif;
    font-size: 22px; color: var(--spec-ink);
  }
  .leaders { position: absolute; inset: 0; pointer-events: none; }
</style>
</head>
<body>
  <section class="label">
    <div class="label__splash" role="img" aria-label="Turquoise brush-stroke splash behind the brand name"></div>
    <div class="label__brand">Dermaloft</div>
    <div class="label__product">Sensitive Cleanser</div>
    <div class="label__mark" role="img" aria-label="Brand emblem placeholder"></div>
    <div class="label__tagline">restore the balance</div>
  </section>

  <div class="spec spec--splash">C:&nbsp; 35<br>M: 5<br>Y:&nbsp; 10<br>K:&nbsp; 0</div>
  <div class="spec__title">Splash</div>
  <div class="spec spec--product">C:&nbsp; 77<br>M: 50<br>Y:&nbsp; 38<br>K:&nbsp; 13</div>
  <div class="spec spec--tagline">C:&nbsp; 50<br>M: 0<br>Y:&nbsp; 100<br>K:&nbsp; 0</div>

  <svg class="leaders" width="1200" height="1200" viewBox="0 0 1200 1200" aria-hidden="true">
    <g stroke="#111" stroke-width="1" fill="none">
      <path d="M126 326 H342 M335 321 L342 326 L335 331"/>
      <path d="M168 450 H392 M385 445 L392 450 L385 455"/>
      <path d="M168 465 H384 M377 460 L384 465 L377 470"/>
      <path d="M208 778 H423 M416 773 L423 778 L416 783"/>
    </g>
  </svg>
</body>
</html>
```